Home Remodeling company needs a business card design

we need a business card design for home remodeling company in hamilton county, indiana USA. we offers a wide range of construction services including whole house renovations, Design and Build Basements and Kitchen and Bathroom Remodeling . we would like to see designs for both site of business card that use the same color of the company logo and also including all information below :
1- Karim Feltous CEO / General Contractor
2- all company contacts Telephone numbers ( 1-888-DULOM-47 ) ( 317-555-0193) email address ( info@dulomhome.com) website ( www.dulomhome.com ) and social media logos (Facebook- twitter- google plus )
3- company logo
4- licensed . insured . bonded

```html
<!DOCTYPE html>
<html lang="en">
<head>
<meta charset="utf-8">
<title>Dulom Business Card</title>
<link rel="stylesheet" href="https://fonts.googleapis.com/css2?family=Open+Sans:wght@400;600;700&display=swap">
<style>
  :root {
    --backdrop: #cfcfcf;
    --card: #1d1d1d;
    --card-edge: #2a2a2a;
    --emboss: #3c3c3c;
    --ink: #ffffff;
    --ink-soft: #d9d9d9;
  }
  * { box-sizing: border-box; margin: 0; padding: 0; }
  html, body {
    width: 1200px; height: 844px; overflow: hidden;
    background: var(--backdrop);
    font-family: "Open Sans", Arial, sans-serif;
  }
  .canvas {
    position: relative; width: 1200px; height: 844px;
    display: flex; align-items: center; justify-content: center; gap: 50px;
  }
  .card {
    position: relative; width: 525px; height: 300px;
    background: radial-gradient(circle at 40% 40%, #232323, var(--card));
    border: 1px solid var(--card-edge);
    box-shadow: 0 10px 24px rgba(0,0,0,.35);
  }
  .brand-name {
    font-family: "Open Sans", Arial, sans-serif;
    font-weight: 700; color: var(--emboss);
    letter-spacing: 3px; line-height: 1;
  }

  /* contact side */
  .card-front .brand-name { position: absolute; left: 44px; top: 122px; font-size: 50px; }
  .contact-block { position: absolute; left: 318px; top: 70px; color: var(--ink); }
  .person-name { font-size: 17px; font-weight: 700; }
  .person-role { font-size: 12px; color: var(--ink-soft); margin-top: 2px; }
  .contact-list { list-style: none; margin-top: 24px; }
  .contact-list li {
    display: flex; align-items: center; gap: 8px;
    font-size: 13.5px; line-height: 21px;
  }
  .contact-list svg { width: 11px; height: 11px; fill: var(--ink); flex: none; }
  .social-row { display: flex; gap: 9px; margin-top: 16px; margin-left: 46px; }
  .social-icon {
    width: 17px; height: 17px; border-radius: 50%; background: var(--ink);
    display: flex; align-items: center; justify-content: center;
  }
  .social-icon svg { width: 10px; height: 10px; fill: var(--card); }

  /* brand side */
  .card-back .brand-name { position: absolute; left: 0; right: 0; top: 108px; text-align: center; font-size: 58px; }
  .credentials {
    position: absolute; left: 0; right: 0; top: 200px; text-align: center;
    color: var(--ink); font-size: 15px; font-weight: 700; letter-spacing: .3px;
  }
</style>
</head>
<body>
<main class="canvas">
  <section class="card card-front" aria-label="Business card contact side">
    <div class="brand-name">DULOM</div>
    <div class="contact-block">
      <p class="person-name">Karim Feltous</p>
      <p class="person-role">CEO / General Contractor</p>
      <ul class="contact-list">
        <li><svg viewBox="0 0 24 24"><path d="M6.6 10.8a15 15 0 0 0 6.6 6.6l2.2-2.2c.3-.3.7-.4 1-.2 1.1.4 2.3.6 3.6.6.6 0 1 .4 1 1V20c0 .6-.4 1-1 1A17 17 0 0 1 3 4c0-.6.4-1 1-1h3.5c.6 0 1 .4 1 1 0 1.3.2 2.5.6 3.6.1.3 0 .7-.2 1z"/></svg>1-888-DULOM-47</li>
        <li><svg viewBox="0 0 24 24"><path d="M6.6 10.8a15 15 0 0 0 6.6 6.6l2.2-2.2c.3-.3.7-.4 1-.2 1.1.4 2.3.6 3.6.6.6 0 1 .4 1 1V20c0 .6-.4 1-1 1A17 17 0 0 1 3 4c0-.6.4-1 1-1h3.5c.6 0 1 .4 1 1 0 1.3.2 2.5.6 3.6.1.3 0 .7-.2 1z"/></svg>317-555-0193</li>
        <li><svg viewBox="0 0 24 24"><path d="M2 5h20v14H2z M2 5l10 8 10-8" fill="none" stroke="#fff" stroke-width="2.5"/></svg>info@dulomhome.com</li>
        <li><svg viewBox="0 0 24 24"><path d="M10 14a4 4 0 0 0 5.7 0l4-4a4 4 0 0 0-5.7-5.7l-1.5 1.5M14 10a4 4 0 0 0-5.7 0l-4 4a4 4 0 0 0 5.7 5.7l1.5-1.5" fill="none" stroke="#fff" stroke-width="2.5"/></svg>www.dulomhome.com</li>
      </ul>
      <div class="social-row" aria-label="Social media links">
        <span class="social-icon"><svg viewBox="0 0 24 24"><path d="M3 4h18v12H9l-5 4v-4H3z"/></svg></span>
        <span class="social-icon"><svg viewBox="0 0 24 24"><circle cx="18" cy="5" r="3.5"/><circle cx="6" cy="12" r="3.5"/><circle cx="18" cy="19" r="3.5"/><path d="M6 12 18 5M6 12l12 7" stroke="#1d1d1d" stroke-width="2.5" fill="none"/></svg></span>
        <span class="social-icon"><svg viewBox="0 0 24 24"><circle cx="12" cy="12" r="9" fill="none" stroke="#1d1d1d" stroke-width="2.5"/><path d="M3 12h18M12 3c-4 5-4 13 0 18M12 3c4 5 4 13 0 18" fill="none" stroke="#1d1d1d" stroke-width="2"/></svg></span>
      </div>
    </div>
  </section>

  <section class="card card-back" aria-label="Business card brand side">
    <div class="brand-name">DULOM</div>
    <p class="credentials">Licensed . Insured . Bonded</p>
  </section>
</main>
</body>
</html>
```